Business card design for holistic health care clinic

We need a double-sided business card design for our holistic health care clinic that integrates our logo design and also its color scheme. My business is called Valmira. It is an integrative medicine clinic. You have already done the logo for me. Please ensure an elegant and upscale design that is not cluttered, but still has all the necessary information (please see below for details).

Target Market(s)

Wellness, fitness, rehabilitation for educated, well-traveled open-minded clients who are focused on natural, organic, balanced and preventive healthcare and lifestyle.

Industry/Entity Type

Medical

Contact Information for Business Card

Modern, clean.

Number of Pages Required

1 page

Font styles to use
Serif
Sans Serif

Colors

Designer to choose colors to be used in the design.

Requirements
Must have
• Logo on one side, all other information on the other side.
• Other information should include:
• Tobias Wrenfeld - DOE, CPT, LMT
• 4100 East Marrow Drive
• Austin, TX 78119
• 512 555 0148
• 818 555 0192
• info@ValmiraHealth.example
• t.wrenfeld@ValmiraHealth.example
Nice to have
• Darker background on front - but not totally black - shaded/dark gray.

```html
<!DOCTYPE html>
<html lang="en">
<head>
<meta charset="utf-8">
<title>Valmira – Business Card</title>
<link rel="stylesheet" href="https://fonts.googleapis.com/css2?family=Open+Sans:ital,wght@0,400;0,600;0,700;1,400&display=swap">
<style>
  :root {
    --stage: #2b2b2d;
    --paper: #f7f7f7;
    --brand-blue: #1a9bd7;
    --brand-blue-deep: #137fb3;
    --charcoal: #2c2d30;
    --ink: #4a4a4a;
    --white: #ffffff;
  }
  * { box-sizing: border-box; margin: 0; padding: 0; }
  html, body {
    width: 1200px; height: 900px; overflow: hidden;
    background: var(--stage);
    font-family: "Open Sans", Arial, sans-serif;
  }
  .canvas {
    width: 1200px; height: 900px;
    display: flex; flex-direction: column;
    align-items: center; justify-content: center; gap: 40px;
  }
  .card {
    position: relative;
    width: 700px; height: 400px;
    overflow: hidden;
    box-shadow: 0 10px 30px rgba(0,0,0,.45);
  }

  /* Front: logo side */
  .card--front {
    background: var(--paper);
    display: flex; flex-direction: column;
    align-items: center; justify-content: center;
  }
  .brand { display: flex; align-items: center; gap: 14px; }
  .brand__dot {
    width: 22px; height: 22px; border-radius: 50%;
    background: var(--brand-blue);
  }
  .brand__name {
    font-weight: 700; color: var(--brand-blue);
    font-size: 78px; letter-spacing: 4px; line-height: 1;
    text-transform: uppercase;
  }
  .brand__descriptor {
    margin-top: 8px;
    color: var(--brand-blue); font-weight: 600;
    font-size: 24px; letter-spacing: .5px;
  }
  .tagline {
    margin-top: 48px;
    color: var(--ink); font-style: italic; font-size: 17px;
  }

  /* Back: contact side */
  .card--back { background: var(--charcoal); }
  .card__split { position: absolute; inset: 0; }
  .contact {
    position: absolute; left: 56px; top: 92px;
    color: var(--white); font-size: 17px; line-height: 1.55;
  }
  .contact__name {
    font-weight: 700; font-size: 20px; letter-spacing: 1px;
    text-transform: uppercase; margin-bottom: 8px;
  }
  .contact__credentials {
    font-size: 12px; font-weight: 700; letter-spacing: .5px;
  }
  .contact__label { font-size: 13px; margin-right: 3px; }
  .back-brand {
    position: absolute; right: 44px; top: 120px;
    text-align: right;
  }
  .back-brand .brand { justify-content: flex-end; }
  .back-brand .brand__name { font-size: 60px; letter-spacing: 3px; }
  .back-brand .brand__dot { width: 18px; height: 18px; }
  .back-brand .brand__descriptor { font-size: 19px; }
</style>
</head>
<body>
<main class="canvas">

  <section class="card card--front" aria-label="Card front">
    <div class="brand">
      <span class="brand__dot"></span>
      <span class="brand__name">Valmira</span>
    </div>
    <p class="brand__descriptor">Integrative Holistic Medicine</p>
    <p class="tagline">it’s all about you – your health, your objectives</p>
  </section>

  <section class="card card--back" aria-label="Card back">
    <svg class="card__split" width="700" height="400" viewBox="0 0 700 400" aria-hidden="true">
      <defs>
        <linearGradient id="blueField" x1="0" y1="0" x2="1" y2="1">
          <stop offset="0" stop-color="#1fa6e0"/>
          <stop offset="1" stop-color="#137fb3"/>
        </linearGradient>
      </defs>
      <path d="M0 0 H330 C300 120 360 260 470 400 H0 Z" fill="url(#blueField)"/>
    </svg>

    <div class="contact">
      <p class="contact__name">Tobias Wrenfeld <span class="contact__credentials">- DOE, CPT, LMT</span></p>
      <p>4100 East Marrow Drive</p>
      <p>Austin, TX 78119</p>
      <p><span class="contact__label">(P)</span>512 555 0148</p>
      <p><span class="contact__label">(C)</span>818 555 0192</p>
      <p>t.wrenfeld@ValmiraHealth.example</p>
      <p>www.ValmiraHealth.example</p>
    </div>

    <div class="back-brand">
      <div class="brand">
        <span class="brand__dot"></span>
        <span class="brand__name">Valmira</span>
      </div>
      <p class="brand__descriptor">Integrative Holistic Medicine</p>
    </div>
  </section>

</main>
</body>
</html>
```